BRTL web site redesign

Coastal Linkage Engineering service (BRTL) is a diverse technology company specialising in design and installation of fibre optics, network convergence and building services, for commercial clients in Australia, we required a new design of our website to attract new clients, generate sales leads, and provide information about our services to the market. The site and should have a new technology look and feel and be designed in word press. our branding colour is blue.

Target Market(s)

New developments, Construction organisations, Commercial end users, IT managers, Consultants.

Industry/Entity Type

It Company

Number of Pages Required

5+ page

Font styles to use
Sans Serif

Colors
0292cd
3176b5

Requirements
Must have
• key pages.
• Home page with some sizzle, automated pictures running through, I like the look of this competitor website http://www.gleamwirex.com.au/ good clean menus and easy to navigate.
• Services page our key services are Fibre optics, Security, Building services,Electrical. I would like the same page layout (Design) for all our services, with a find out more link on each page, manly picture driven with text around our key messaging.
• About us page with space for company profile and directors pictures, bio and contact information.
• Certifications / Accreditations page with have over 20 certifications on different products from suppliers, and a number of licences from governing bodies.
• Current and past projects page with case studies and customer outcomes
• Contact us page with options around what services they require more information on, please keep in mind the site is around generating sales Leeds and being seen as an industry expert.
Nice to have
• RSS feeds, Linked in link, to be placed within the design, Consistent BRTL branding,Same colour blue as our logo Document library for education information, white papers, presentations etc,
• a new technology look and feel, mobile friendly.
Should not have
• boring layout, move away from our cuurent website http://www.brtlgroup.com.au/
• no e eCommerce store required.

```html
<!DOCTYPE html>
<html lang="en">
<head>
<meta charset="utf-8">
<title>BRTL – Security Services</title>
<link href="https://fonts.googleapis.com/css2?family=Roboto:wght@300;400;500;700&display=swap" rel="stylesheet">
<style>
:root{
  --sky:#0292cd;
  --brand:#3176b5;
  --title:#1f6fb2;
  --dark:#333333;
  --black:#111111;
  --text:#333333;
  --muted:#555555;
  --light:#eeeeee;
  --rule:#c9c9c9;
}
*{box-sizing:border-box;margin:0;padding:0}
html,body{width:977px;height:1200px;overflow:hidden;background:#fff}
body{font-family:'Roboto',Arial,sans-serif;color:var(--text);position:relative}
.abs{position:absolute}

.topbar{left:0;top:0;width:977px;height:37px;background:var(--sky)}
.navbar{left:0;top:37px;width:977px;height:63px;background:var(--dark)}
.top-phone{right:137px;top:12px;color:#fff;font-size:12px;display:flex;align-items:center;gap:6px}
.signin{left:855px;top:8px;width:51px;height:20px;border:1px solid #fff;border-radius:3px;color:#fff;font-size:9px;text-align:center;line-height:18px}
.brand{left:73px;top:11px;width:176px;height:89px;background:#fff;padding:4px}
.brand-inner{width:100%;height:100%;background:var(--sky);display:flex;align-items:center;justify-content:center;gap:8px;color:#fff;font-weight:700;font-size:30px;letter-spacing:1px}
.brand-inner i{width:14px;height:14px;background:#fff;display:block}
.nav{top:70px;left:371px;display:flex;font-size:10.5px;color:#fff}
.nav span{position:absolute;white-space:nowrap}
.nav .active{color:var(--sky)}

.page-title{left:74px;top:147px;font-size:22px;font-weight:500;color:var(--title)}
.title-rule{left:74px;top:183px;width:593px;height:1px;background:#888}
.intro{left:75px;top:199px;width:580px;font-size:12px;line-height:19px;color:#333}
.subhead{left:74px;top:250px;font-size:13.5px;color:var(--sky)}
.photo-main{left:77px;top:284px;width:185px;height:139px;background:linear-gradient(160deg,#9fc2e3,#4f7fae 55%,#7b8da0)}
.features{left:303px;top:284px;list-style:none;font-size:11.5px;line-height:21.5px;color:#333}
.features li::before{content:"»";color:var(--brand);margin-right:6px}
.para{left:74px;width:579px;font-size:11.3px;line-height:18.5px;color:#333;text-align:justify}
.product{top:643px;height:65px;background:linear-gradient(#f4f4f4,#e3e3e3)}
.product-label{top:726px;font-size:9.5px;color:var(--brand);white-space:nowrap}

.contact-card{left:674px;top:149px;width:233px;height:384px;background:linear-gradient(#ececec,#f6f6f6);border:1px solid #c7c7c7}
.contact-card h2{position:absolute;left:19px;top:17px;font-size:14px;font-weight:500;color:var(--title)}
.card-note{position:absolute;left:20px;top:43px;font-size:8.5px;line-height:14px;color:#333}
.card-rule{position:absolute;left:20px;top:76px;width:187px;height:1px;background:#c5c5c5}
.label{position:absolute;left:21px;font-size:9px;color:#333}
.field{position:absolute;background:#fff;border:1px solid #bbb;box-shadow:inset 0 2px 2px #ccc;font-size:8.5px;color:#666;padding:6px 7px}
.submit{position:absolute;left:21px;top:340px;width:76px;height:26px;background:#2b2b2b;color:#fff;font-size:10px;text-align:center;line-height:26px;box-shadow:0 2px 3px #999}
.card-shadow{left:690px;top:533px;width:200px;height:14px;background:radial-gradient(ellipse at top,rgba(0,0,0,.18),transparent 70%)}

.promo{left:675px;top:554px;width:232px;height:186px;background:var(--brand);border:1px solid #2a5f93;color:#fff}
.promo h3{position:absolute;left:18px;top:32px;font-size:12px;font-weight:500}
.promo p{position:absolute;left:19px;top:57px;width:180px;font-size:8.5px;line-height:15.7px;text-align:justify}
.promo-btn{position:absolute;left:19px;top:142px;width:75px;height:26px;background:linear-gradient(#fff,#ddd);color:#333;font-size:9.5px;text-align:center;line-height:26px;border-radius:2px}

.callband{left:0;top:789px;width:977px;height:107px;background:var(--brand)}
.call-text{left:153px;top:822px;font-size:32px;font-weight:300;color:#fff}
.call-btn{left:652px;top:819px;width:224px;height:48px;background:linear-gradient(#1ca8e2,#0a8cc6);border:1px solid #7cc8ee;border-radius:3px;color:#fff;font-size:18px;font-weight:500;text-align:center;line-height:46px}

.footer-top{left:0;top:896px;width:977px;height:180px;background:var(--light)}
.foot-head{top:927px;font-size:13.5px;color:var(--title)}
.foot-small{font-size:8.5px;line-height:15px;color:#444}
.news-thumb{width:51px;height:42px;border:2px solid #fff;box-shadow:0 1px 3px #999}
.news-date{color:var(--sky)}
.rss-icon{left:685px;top:992px;width:47px;height:47px;border-radius:7px;background:linear-gradient(#fca64a,#f07c12)}

.footer-bottom{left:0;top:1076px;width:977px;height:124px;background:var(--black);color:#fff}
.foot-links{left:74px;top:1118px;font-size:10px}
.copy{left:74px;top:1136px;font-size:10px}
.social-head{left:615px;top:1123px;font-size:10px}
.social-note{left:615px;top:1141px;font-size:8.5px}
.social{top:1117px;width:30px;height:30px;border-radius:50%;border:2px solid #ddd}
</style>
</head>
<body>

<header>
  <div class="abs topbar"></div>
  <div class="abs navbar"></div>
  <div class="abs top-phone">
    <svg width="12" height="12" viewBox="0 0 12 12"><rect width="12" height="12" rx="2" fill="#fff"/><path d="M3.5 2.5l1.5 1.5-.8 1a5 5 0 0 0 2.8 2.8l1-.8 1.5 1.5-1 1.2C5.5 9.5 2.5 6.5 2.3 3.5z" fill="var(--sky)"/></svg>
    1300 555 019
  </div>
  <div class="abs signin">SIGN IN</div>
  <div class="abs brand"><div class="brand-inner"><i></i>BRTL</div></div>
  <nav class="abs nav">
    <span style="left:0">HOME</span>
    <span class="active" style="left:51px">SERVICES »</span>
    <span style="left:131px">ABOUT US</span>
    <span style="left:203px">CERTIFICATIONS</span>
    <span style="left:313px">CURRENT / PAST PROJECTS</span>
    <span style="left:474px">CONTACT US</span>
  </nav>
</header>

<main>
  <h1 class="abs page-title">SECURITY SERVICES</h1>
  <div class="abs title-rule"></div>
  <p class="abs intro">BRTL offers a wide range of IP commercial security solutions, from a small standalone system to our fully integrated enterprise systems,</p>
  <h2 class="abs subhead" style="font-weight:400">Solutions that BRTL offers are.</h2>
  <div class="abs photo-main" role="img" aria-label="Collage of office towers, a card access reader and a security camera"></div>
  <ul class="abs features">
    <li>Access control</li><li>IP CCTV</li><li>Intercoms</li><li>Intruder systems</li>
    <li>Visitor management</li><li>Perimeter detection</li><li>Mobile and fixed duress</li>
  </ul>
  <p class="abs para" style="top:449px">Our experience in providing security solutions to our clients enables Design and construct capabilities as well as responding to consultant / builder briefs through your procurement process.</p>
  <p class="abs para" style="top:497px">Where BRTL differentiates our solutions from the pack is by the use of technology advancements such as security applications on your smart device which enables you full control of your systems any time anywhere. Your security applications can also be hosted by BRTL reducing the costly software and hardware upgrades.</p>
  <p class="abs para" style="top:566px">Further to the applications BRTL takes a holistic approach in designing your network, a large number of our clients take advantage of the BRTL capabilities in our voice and data network offerings this allows the IP security network to reside on the Voice and data network, this layer of convergence reduces capital investment and ongoing maintenance due to a single network.</p>

  <div class="abs product" style="left:85px;width:87px" role="img" aria-label="Access control hardware units"></div>
  <div class="abs product" style="left:240px;width:86px" role="img" aria-label="CCTV monitoring screens"></div>
  <div class="abs product" style="left:386px;width:87px" role="img" aria-label="Intruder alarm panel and sensors"></div>
  <div class="abs product" style="left:550px;width:87px" role="img" aria-label="Intercom handset unit"></div>
  <div class="abs product-label" style="left:76px">Access Control Systems</div>
  <div class="abs product-label" style="left:258px">CCTV</div>
  <div class="abs product-label" style="left:372px">Intruder &amp; Alarm systems</div>
  <div class="abs product-label" style="left:540px">Intercoms &amp; Help points</div>

  <aside>
    <form class="abs contact-card">
      <h2>CONTACT BRTL</h2>
      <p class="card-note">Please contact us on 1300 555 019<br>or fill out below</p>
      <div class="card-rule"></div>
      <span class="label" style="top:87px;font-size:10px">Contact Name</span>
      <div class="field" style="left:20px;top:107px;width:89px;height:25px">First</div>
      <div class="field" style="left:112px;top:107px;width:91px;height:25px">Last</div>
      <span class="label" style="top:148px">Email Address</span>
      <div class="field" style="left:21px;top:164px;width:188px;height:25px"></div>
      <span class="label" style="top:199px">Primary Contact Phone</span>
      <div class="field" style="left:21px;top:216px;width:188px;height:25px"></div>
      <span class="label" style="top:257px">How can we help you today?</span>
      <div class="field" style="left:21px;top:274px;width:188px;height:58px"></div>
      <div class="submit">SUBMIT</div>
    </form>
    <div class="abs card-shadow"></div>
    <div class="abs promo">
      <h3>LOREM IPSUM IS SIMPLY DUMMY</h3>
      <p>Lorem Ipsum has been the industry's standard dummy text ever since the 1500s, when an unknown printer took a galley of type and scrambled it to make a type specimen book. It has survived not only five centuries</p>
      <div class="promo-btn">CLICK HERE</div>
    </div>
  </aside>

  <section>
    <div class="abs callband"></div>
    <svg class="abs" style="left:86px;top:819px" width="48" height="48" viewBox="0 0 48 48"><circle cx="24" cy="24" r="22" fill="none" stroke="#fff" stroke-width="3"/><path d="M16 13l4 4-2 3a14 14 0 0 0 10 10l3-2 4 4-3 3c-9-1-18-10-19-19z" fill="#fff"/></svg>
    <div class="abs call-text">Call Us Today ! 1300 555 019</div>
    <div class="abs call-btn">CONTACT US</div>
  </section>
</main>

<footer>
  <div class="abs footer-top"></div>
  <h3 class="abs foot-head" style="left:72px;font-weight:400">CONTACT INFO</h3>
  <p class="abs foot-small" style="left:75px;top:955px">Suite 4B. 12-14 Harbour Lane<br>Seaview NSW 2190<br>PO Box 2048 NSW 1830</p>
  <div class="abs foot-small" style="left:75px;top:1009px;font-size:9.5px;line-height:18px">
    <div><span style="color:var(--brand)">✆</span>&nbsp;&nbsp; 1300 555 019</div>
    <div><span style="color:var(--brand)">✉</span>&nbsp;&nbsp; info@brtlmail.com</div>
  </div>

  <h3 class="abs foot-head" style="left:324px;font-weight:400;top:925px">LATEST NEWS</h3>
  <div class="abs news-thumb" style="left:324px;top:955px;background:linear-gradient(135deg,#5c8a6a,#cfd9d0)" role="img" aria-label="Aerial view of a city"></div>
  <p class="abs foot-small" style="left:387px;top:955px;width:210px">Lorem ipsum dolor sit amet, consectetur adipisicing elit, sed do eiusmod tempor<br><span class="news-date">july 7, 2015</span></p>
  <div class="abs news-thumb" style="left:324px;top:1010px;background:linear-gradient(135deg,#8ab8d8,#d9b8a0)" role="img" aria-label="Street scene with buildings"></div>
  <p class="abs foot-small" style="left:388px;top:1010px;width:210px">Lorem ipsum dolor sit amet, consectetur adipisicing elit, sed do eiusmod tempor<br><span class="news-date">july 7, 2015</span></p>

  <h3 class="abs foot-head" style="left:685px;font-weight:400">RSS FEED</h3>
  <p class="abs foot-small" style="left:686px;top:952px;width:225px">Lorem ipsum dolor sit amet, consectetur adipisicing elit, sed do eiusmod tempor</p>
  <div class="abs rss-icon" role="img" aria-label="Feed icon"></div>
  <p class="abs foot-small" style="left:740px;top:997px;width:165px">Lorem ipsum dolor sit amet, consectetur adipisicing elit, sed do eiusmod tempor<br><span style="color:#f08a1c;text-decoration:underline">Links</span></p>

  <div class="abs footer-bottom"></div>
  <div class="abs foot-links" style="color:#fff">HOME &nbsp;|&nbsp; ABOUT &nbsp;|&nbsp; NEWS &nbsp;|&nbsp; BLOG &nbsp;|&nbsp; CONTACTS</div>
  <div class="abs copy" style="color:#fff">© 2015 &nbsp;Privacy Policy</div>
  <div class="abs social-head" style="color:#fff">SOCIAL NETWORKS</div>
  <div class="abs social-note" style="color:#fff">Lorem Ipsum is simply dummy text</div>
  <div class="abs social" style="left:773px;background:#3b5b99" role="img" aria-label="Social network link"></div>
  <div class="abs social" style="left:808px;background:#d6453a" role="img" aria-label="Social network link"></div>
  <div class="abs social" style="left:843px;background:#2a9de0" role="img" aria-label="Social network link"></div>
  <div class="abs social" style="left:878px;background:#f4731c" role="img" aria-label="Feed link"></div>
</footer>

</body>
</html>
```